Walk Beside The River

Business Card design

Target Market(s)

People who require support in the commnity

Industry/Entity Type

Mental Health Support

Contact Information for Business Card

Mental Health Support Rosalind Tavener walkbesidetheriver@mailcove.com.au 0481 637 092 PO Box 926 Kelvale QLD 4571

Colors
6B429C
8869AF
B7A5CE
E3DAEB
F3F0F8

Requirements
Must have
• Logo & details listed above
Should not have
• No red or orange

```html
<!DOCTYPE html>
<html lang="en">
<head>
<meta charset="utf-8">
<title>Walk Beside The River – Business Card</title>
<link href="https://fonts.googleapis.com/css2?family=Open+Sans:wght@400;700;800&display=swap" rel="stylesheet">
<style>
  :root {
    --page: #2b2b2f;
    --card: #1d1d21;
    --purple: #6b429c;
    --purple-name: #7a4fb3;
    --yellow: #e8e22c;
    --ink: #f3f0f8;
    --silver: #8a8a90;
  }
  * { margin: 0; padding: 0; box-sizing: border-box; }
  html, body {
    width: 1200px; height: 780px; overflow: hidden;
    background: var(--page);
    font-family: "Open Sans", Arial, sans-serif;
  }
  .canvas {
    width: 1200px; height: 780px;
    display: flex; align-items: center; justify-content: center; gap: 40px;
  }
  .card {
    position: relative;
    width: 540px; height: 310px;
    background: var(--card);
    border-radius: 4px;
    box-shadow: 0 10px 30px rgba(0,0,0,.45);
    overflow: hidden;
  }

  /* Front */
  .brand {
    position: absolute; left: 30px; top: 30px;
    display: flex; align-items: center; gap: 12px;
  }
  .brand-dot {
    width: 58px; height: 58px; border-radius: 50%;
    background: var(--purple);
  }
  .brand-name {
    color: var(--ink); font-weight: 700; font-size: 14px;
    letter-spacing: .12em; text-transform: uppercase; line-height: 1.4;
    width: 150px;
  }
  .holder {
    position: absolute; right: 46px; top: 110px; text-align: right;
  }
  .holder-name {
    font-weight: 800; font-size: 30px; line-height: 1.1;
  }
  .holder-name .first { color: var(--yellow); }
  .holder-name .last { color: var(--purple-name); }
  .holder-role {
    color: var(--ink); font-size: 14px; margin-top: 4px;
  }
  .edge-band {
    position: absolute; right: 0; top: 108px;
    width: 22px; height: 76px; background: var(--yellow);
  }
  .details {
    position: absolute; left: 30px; bottom: 26px;
    color: var(--ink); font-size: 12.5px; line-height: 1.55;
  }
  .details .line { display: flex; align-items: center; gap: 8px; }
  .details .icon { width: 12px; height: 12px; flex: none; }
  .details .contact-person { margin-bottom: 6px; }

  /* Back */
  .pattern {
    position: absolute; inset: 0;
    background: linear-gradient(110deg, #1a1a1e 0%, #202024 50%, #4a4a50 78%, var(--silver) 100%);
  }
</style>
</head>
<body>
<main class="canvas">
  <section class="card card-front" aria-label="Business card front">
    <div class="brand">
      <span class="brand-dot"></span>
      <span class="brand-name">Walk Beside The River</span>
    </div>

    <div class="holder">
      <p class="holder-name"><span class="first">Mirela</span> <span class="last">Voskova</span></p>
      <p class="holder-role">CEO/Director</p>
    </div>
    <span class="edge-band"></span>

    <div class="details">
      <p class="service">Mental Health Support</p>
      <p class="contact-person">Rosalind Tavener</p>
      <p class="line">
        <svg class="icon" viewBox="0 0 24 24" aria-hidden="true"><path fill="var(--yellow)" d="M6.6 10.8a15.1 15.1 0 0 0 6.6 6.6l2.2-2.2a1 1 0 0 1 1-.25 11.4 11.4 0 0 0 3.6.57 1 1 0 0 1 1 1V20a1 1 0 0 1-1 1A17 17 0 0 1 3 4a1 1 0 0 1 1-1h3.5a1 1 0 0 1 1 1c0 1.25.2 2.45.57 3.57a1 1 0 0 1-.25 1z"/></svg>
        <span>0481 637 092</span>
      </p>
      <p class="line">
        <svg class="icon" viewBox="0 0 24 24" aria-hidden="true"><rect x="2" y="5" width="20" height="14" rx="2" fill="none" stroke="var(--yellow)" stroke-width="2"/><path d="M3 6l9 7 9-7" fill="none" stroke="var(--yellow)" stroke-width="2"/></svg>
        <span>walkbesidetheriver@mailcove.com.au</span>
      </p>
      <p class="line">
        <svg class="icon" viewBox="0 0 24 24" aria-hidden="true"><path fill="var(--yellow)" d="M12 2a7 7 0 0 0-7 7c0 5.2 7 13 7 13s7-7.8 7-13a7 7 0 0 0-7-7zm0 9.5A2.5 2.5 0 1 1 12 6.5a2.5 2.5 0 0 1 0 5z"/></svg>
        <span>PO Box 926 Kelvale QLD 4571</span>
      </p>
    </div>
  </section>

  <section class="card card-back" aria-label="Business card back">
    <div class="pattern" role="img" aria-label="Repeating star pattern on black, fading to silver on the right"></div>
  </section>
</main>
</body>
</html>
```